Mortgage Specialist Wordpress Build

I have a current WordPress site but I would like a whole new site built using the same domain. I've included a site for reference in my outline. The main focus of the website is to educate and capture leads.
I would like my blogs to stay for SEO already earned. Please see work requested attached.
Updates
Project Deadline Extended Reason: I am extending the deadline because I didn't realize this was a design only and I need the website coded as well. I've purchased the add-on. This is my first time using Pixel Harbor so please bare with me. I have additional Wordpress sites I want to have built too. Thanks, Colin Added Tuesday, April 18, 2017
Target Market(s)
Home Buyers, Home owners looking to refinance or renew their mortgages
Industry/Entity Type
Mortgage
Coding
Coded - Design and coding required
Font styles to use
Look and feel
Each slider illustrates characteristics of the customer's brand and the style your logo design should communicate.

```html
<!DOCTYPE html>
<html lang="en">
<head>
<meta charset="utf-8">
<title>Harbourline Mortgage Group – North Vancouver Mortgage Broker</title>
<link href="https://fonts.googleapis.com/css2?family=Open+Sans:wght@400;600;700&family=Raleway:wght@600;700;800&family=Lobster&display=swap" rel="stylesheet">
<style>
:root{
  --navy:#1d4f91;
  --navy-dark:#163f75;
  --gold:#f0c31c;
  --card:#f8e9a6;
  --ink:#2b2b2b;
  --grey:#777;
  --light:#f6f6f6;
  --white:#fff;
}
*{box-sizing:border-box;margin:0;padding:0}
html,body{width:1200px;height:2557px;overflow:hidden}
body{font-family:"Open Sans",Arial,sans-serif;color:var(--ink);background:var(--white);position:relative}
.abs{position:absolute}

/* header */
.site-header{position:absolute;left:0;top:0;width:1200px;height:92px;background:var(--navy)}
.brand{position:absolute;left:100px;top:30px;display:flex;align-items:center;gap:10px;color:var(--white);font-family:"Raleway",sans-serif;font-weight:700;font-size:17px;letter-spacing:.3px}
.brand-mark{width:26px;height:26px;border:2px solid var(--white);border-radius:50%}
.main-nav{position:absolute;top:36px;left:0;width:100%;font-family:"Raleway",sans-serif;font-weight:700;font-size:14px;color:var(--white)}
.main-nav span{position:absolute}
.main-nav .active{color:var(--gold)}
.btn-signin{position:absolute;left:1008px;top:25px;width:92px;height:42px;background:var(--gold);color:var(--white);font-family:"Raleway",sans-serif;font-weight:700;font-size:14px;display:flex;align-items:center;justify-content:center;border-radius:2px}

/* hero */
.hero{position:absolute;left:0;top:92px;width:1200px;height:483px;background:linear-gradient(90deg,#8a8f96 0%,#b9bcc0 30%,#9a9ea4 60%,#5c6168 100%)}
.hero::after{content:"";position:absolute;inset:0;background:rgba(20,25,35,.35)}
.hero-content{position:absolute;z-index:1;left:0;width:100%;text-align:center;color:var(--white)}
.hero-title{top:160px;font-family:"Raleway",sans-serif;font-weight:800;font-size:50px;letter-spacing:.5px}
.hero-sub{top:231px;font-size:17px}
.btn-hooked{position:absolute;z-index:1;left:432px;top:290px;width:167px;height:53px;background:var(--gold);color:var(--white);font-family:"Raleway",sans-serif;font-weight:700;font-size:17px;display:flex;align-items:center;justify-content:center}
.btn-client{position:absolute;z-index:1;left:617px;top:290px;width:151px;height:53px;border:2px solid var(--white);color:var(--white);font-family:"Raleway",sans-serif;font-weight:700;font-size:17px;display:flex;align-items:center;justify-content:center}
.play{position:absolute;z-index:1;left:576px;top:374px}

/* partners */
.partners{position:absolute;left:0;top:575px;width:1200px;height:150px;background:var(--light);display:flex;justify-content:space-around;align-items:center;padding:0 100px}
.partner-badge{width:110px;height:40px;background:#d9dde2;border-radius:4px}

/* help */
.help-title{position:absolute;top:785px;width:100%;text-align:center;font-size:35px;font-weight:400;color:#222}
.help-card{position:absolute;top:873px;width:318px;height:331px;background:var(--card);text-align:center}
.help-card svg{position:absolute;left:50%;transform:translateX(-50%);top:48px}
.help-card h3{position:absolute;top:137px;width:100%;font-size:19px;font-weight:600;color:#222}
.help-card p{position:absolute;top:178px;left:18px;right:18px;font-size:12.5px;line-height:23px;color:#444}
.btn-apply{position:absolute;top:243px;left:108px;width:102px;height:40px;border:1.5px solid var(--navy);font-size:11.5px;font-weight:600;color:var(--navy);display:flex;align-items:center;justify-content:center}

/* questions */
.questions{position:absolute;left:0;top:1277px;width:1200px;height:275px;background:linear-gradient(120deg,#1f2226,#3a3d42 50%,#24272b)}
.questions h2{position:absolute;top:58px;width:100%;text-align:center;color:var(--white);font-family:"Raleway",sans-serif;font-weight:700;font-size:38px}
.search{position:absolute;left:215px;top:155px;width:770px;height:55px;background:var(--white);border-radius:3px}
.search span{position:absolute;left:32px;top:19px;font-size:11px;color:#999}
.search .ask{position:absolute;right:0;top:0;width:90px;height:55px;background:var(--gold);color:var(--white);font-weight:700;font-size:16px;display:flex;align-items:center;justify-content:center;border-radius:0 3px 3px 0}

/* about */
.about{position:absolute;left:0;top:1552px;width:1200px;height:608px;background:#f7f7f8}
.portrait{position:absolute;left:97px;top:86px;width:333px;height:436px;background:linear-gradient(160deg,#4a4e53,#2a2c30)}
.about h2{position:absolute;left:473px;top:95px;font-size:26px;font-weight:400;color:#222}
.about p{position:absolute;left:475px;width:640px;font-size:12px;line-height:28.5px;color:var(--grey)}
.reach{position:absolute;left:475px;top:392px;font-family:"Lobster",cursive;font-size:23px;color:var(--gold)}
.btn-app{position:absolute;left:475px;top:452px;width:239px;height:52px;border:1.5px solid var(--navy);display:flex;align-items:center;justify-content:center;gap:8px;font-size:12.5px;font-weight:600;color:var(--navy);background:var(--white)}
.share{position:absolute;left:745px;top:458px;display:flex;gap:7px}
.share span{width:36px;height:36px;background:var(--navy);border-radius:4px}

/* footer */
.site-footer{position:absolute;left:0;top:2160px;width:1200px;height:397px;background:var(--white);border-top:3px solid var(--navy)}
.f-head{position:absolute;top:62px;font-family:"Raleway",sans-serif;font-weight:600;font-size:15px;color:#222}
.f-item{position:absolute;font-size:12.5px;color:#444;line-height:22px}
.f-icon{position:absolute}
.social-dot{position:absolute;width:26px;height:26px;border:1.3px solid #555;border-radius:50%}
.newsletter-input{position:absolute;left:571px;top:155px;width:262px;height:42px;border:1px solid #ccc;font-size:11px;color:#666;padding:14px 12px}
.btn-subscribe{position:absolute;left:571px;top:215px;width:100px;height:40px;background:var(--navy);color:var(--white);font-size:12.5px;font-weight:700;display:flex;align-items:center;justify-content:center}
.footer-brand{position:absolute;left:885px;top:70px;width:220px;text-align:center;font-family:"Raleway",sans-serif;font-weight:700;font-size:18px;color:#222;line-height:26px}
.anniv{position:absolute;left:960px;top:188px;width:70px;height:70px;border-radius:50%;background:var(--navy-dark)}
.footer-rule{position:absolute;left:97px;top:318px;width:1006px;height:1px;background:#e3e3e3}
.copyright{position:absolute;top:347px;width:100%;text-align:center;font-size:12.5px;color:#444}
</style>
</head>
<body>

<header class="site-header">
  <div class="brand"><span class="brand-mark"></span>Harbourline Mortgage Group</div>
  <nav class="main-nav">
    <span class="active" style="left:535px">Home</span>
    <span style="left:660px">About</span>
    <span style="left:785px">Blog</span>
    <span style="left:900px">Contact</span>
  </nav>
  <div class="btn-signin">SIGN IN</div>
</header>

<section class="hero" role="img" aria-label="Photo of a couple shaking hands with a mortgage broker in a bright living room">
  <h1 class="hero-content hero-title abs">BUYING YOUR DREAM HOME</h1>
  <p class="hero-content hero-sub abs">Take the guess work out of the home buying process – Free eBook is yours</p>
  <div class="btn-hooked">Get Hooked Up</div>
  <div class="btn-client">I'm a client</div>
  <svg class="play" width="48" height="48" viewBox="0 0 48 48"><circle cx="24" cy="24" r="21" fill="none" stroke="#fff" stroke-width="3"/><path d="M19 15l14 9-14 9z" fill="#fff"/></svg>
</section>

<section class="partners" aria-label="Lending partners">
  <span class="partner-badge"></span><span class="partner-badge"></span><span class="partner-badge"></span>
  <span class="partner-badge"></span><span class="partner-badge"></span><span class="partner-badge"></span>
</section>

<h2 class="help-title">I need help with</h2>

<article class="help-card" style="left:99px">
  <svg width="80" height="74" viewBox="0 0 80 74"><path d="M40 4L4 36h10v34h20V50h12v20h20V36h10z" fill="var(--navy)"/><rect x="56" y="8" width="9" height="18" fill="var(--navy)"/></svg>
  <h3>Purchase</h3>
  <p>Purchasing a home can be a daunting task as the market continues to sizzle essential...</p>
  <div class="btn-apply">APPLY NOW</div>
</article>

<article class="help-card" style="left:441px">
  <svg width="82" height="82" viewBox="0 0 82 82" fill="none" stroke="var(--navy)" stroke-width="5"><path d="M12 30A31 31 0 0 1 68 22"/><path d="M70 52A31 31 0 0 1 14 60"/><path d="M68 8v15H53M14 74V59h15"/><text x="41" y="52" text-anchor="middle" font-family="Open Sans,sans-serif" font-size="32" font-weight="700" fill="var(--navy)" stroke="none">$</text></svg>
  <h3 style="top:140px">Refinance</h3>
  <p style="top:181px">Want to pull out some equity or need to sell your property? you need to consolidate...</p>
  <div class="btn-apply" style="top:246px">APPLY NOW</div>
</article>

<article class="help-card" style="left:783px">
  <svg width="70" height="70" viewBox="0 0 70 70" fill="none" stroke="var(--navy)" stroke-width="3"><path d="M8 30A28 28 0 0 1 58 18"/><path d="M62 40A28 28 0 0 1 12 52"/><path d="M58 6v12H46M12 64V52h12"/></svg>
  <h3 style="top:133px">Renewal</h3>
  <p style="top:172px">It's best to start looking for new financing 120 days<br>It's neve before your maturity.....</p>
  <div class="btn-apply" style="top:238px">APPLY NOW</div>
</article>

<section class="questions" role="img" aria-label="Dark photo of a desk with a tablet and keyboard">
  <h2>Mortgage or Real Estate Questions?</h2>
  <div class="search"><span>Search Our Knowlede base....</span><div class="ask">ASK</div></div>
</section>

<section class="about">
  <div class="portrait" role="img" aria-label="Portrait photo of the mortgage broker"></div>
  <h2>North Vancouver Mortgage Broker</h2>
  <p style="top:148px">Purchasing a home, refinancing a mortgage and renewing a mortgage have one thing in common: they can represent an exciting time in an individual's life but they can also be complex.I am dedicated to giving back to the region by helping people save thousands of dollars in interest and prepayment expenses and find solutions that are fitted to your specific situation.</p>
  <p style="top:267px">In addition to getting you a fantastic rate, I ensure that I take enough time for each and every one of my clients to go over every detail in order to see that their mortgage repayment schedule is on track with their financial objectives. It is my mission to help people in this wonderful area get the best North Vancouver mortgage package possible while providing tremendous care and service.</p>
  <div class="reach">You can reach me at 604.555.0142</div>
  <div class="btn-app"><svg width="11" height="12" viewBox="0 0 11 12"><path d="M4 0h3v6h3L5.5 10 1 6h3zM0 11h11v1H0z" fill="var(--navy)"/></svg>Download My Mortgage App</div>
  <div class="share"><span></span><span></span><span></span><span></span><span></span></div>
</section>

<footer class="site-footer">
  <h4 class="f-head" style="left:96px">CONTACT US</h4>
  <svg class="f-icon" style="left:96px;top:110px" width="14" height="20" viewBox="0 0 14 20" fill="none" stroke="#333" stroke-width="1.5"><path d="M7 19S1 11 1 7a6 6 0 0 1 12 0c0 4-6 12-6 12z"/><circle cx="7" cy="7" r="2.2"/></svg>
  <div class="f-item" style="left:130px;top:108px">415 Harbourview Ave.<br>North Vancouver, BC V7M 0A1</div>
  <svg class="f-icon" style="left:96px;top:165px" width="18" height="16" viewBox="0 0 18 16" fill="none" stroke="#333" stroke-width="1.5"><path d="M2 2c3-2 4 2 5 4l-2 2c1 2 3 4 5 5l2-2c2 1 6 2 4 5-3 3-14-6-14-14z"/></svg>
  <div class="f-item" style="left:130px;top:162px">Phone :&nbsp; (604).555.0142</div>
  <svg class="f-icon" style="left:96px;top:210px" width="18" height="16" viewBox="0 0 18 16" fill="none" stroke="#333" stroke-width="1.5"><rect x="1" y="5" width="16" height="10"/><rect x="4" y="1" width="10" height="4"/><path d="M5 9h8M5 12h8"/></svg>
  <div class="f-item" style="left:130px;top:206px">Fax: 604.555.0187</div>
  <svg class="f-icon" style="left:96px;top:256px" width="20" height="14" viewBox="0 0 20 14" fill="none" stroke="#333" stroke-width="1.5"><rect x="1" y="1" width="18" height="12"/><path d="M1 1l9 7 9-7"/></svg>
  <div class="f-item" style="left:130px;top:251px">colin@harbourlinemortgage.ca</div>

  <h4 class="f-head" style="left:386px;top:58px">SOCIAL MEDIA</h4>
  <span class="social-dot" style="left:388px;top:113px"></span><div class="f-item" style="left:430px;top:115px">Neighbourly</div>
  <span class="social-dot" style="left:388px;top:157px"></span><div class="f-item" style="left:430px;top:159px">Chirpline</div>
  <span class="social-dot" style="left:388px;top:200px"></span><div class="f-item" style="left:430px;top:202px">Circlesphere</div>
  <span class="social-dot" style="left:388px;top:243px"></span><div class="f-item" style="left:430px;top:245px">Workweb</div>

  <h4 class="f-head" style="left:571px">SIGNUP OUR NEWSLETTER</h4>
  <div class="f-item" style="left:571px;top:95px;width:270px;font-size:11.5px">Add your email below to receive my monthly mortgage update &amp; to join our VIP Club.</div>
  <div class="newsletter-input">Enter Mail</div>
  <div class="btn-subscribe">SUBSCRIBE</div>

  <div class="footer-brand">Harbourline<br>Mortgage Group</div>
  <div class="anniv"></div>

  <div class="footer-rule"></div>
  <div class="copyright">© Copyright&nbsp; Harbourline Mortgage Group ,2017. All rights reserved.</div>
</footer>

</body>
</html>
```